VFX Company Business Card Design Project

The Kestrel Works is a decentralized Visual Effects Studio servicing the television and feature film industries.
Project Brief:
Take our logo that was previously designed on Pencil Harbor and make a double sided business card.
Requirements:
- Card MUST be double sided.
- Front of card MUST have the yellow part of our logo against the dark grey background.
- Back of card is completely up to the designer.
- Back of card must include the complete company logo.
Please follow these File Preparation guidelines:
http://printnook.ca/infopage?file=filetype_en&s=PrintNook_new&lang=en
Business

```html
<!DOCTYPE html>
<html lang="en">
<head>
<meta charset="utf-8">
<title>The Kestrel Works – Business Cards</title>
<link rel="stylesheet" href="https://fonts.googleapis.com/css2?family=Josefin+Sans:wght@300;400;700&family=Open+Sans:wght@400;700&display=swap">
<style>
  :root {
    --backdrop: #8a4a22;
    --card-dark: #2a2a2a;
    --brand-yellow: #fcc42a;
    --brand-grey: #5f686c;
    --paper: #eef0e8;
    --ink-light: #f2f2ee;
    --ink-mid: #5b6468;
    --rule: #4d5558;
  }
  * { box-sizing: border-box; margin: 0; padding: 0; }
  html, body { width: 1200px; height: 734px; overflow: hidden; }
  body {
    position: relative;
    background: var(--backdrop);
    font-family: "Open Sans", sans-serif;
  }
  .card {
    position: absolute;
    width: 524px;
    height: 300px;
    background: var(--card-dark);
    color: var(--ink-light);
    overflow: hidden;
  }
  .card--front { left: 67px; top: 43px; }
  .card--contact { left: 628px; top: 48px; }
  .card--lockup { left: 63px; top: 381px; }
  .card--wordmark { left: 622px; top: 387px; }

  .brand-name {
    position: absolute;
    left: 0; right: 0;
    text-align: center;
    font-family: "Josefin Sans", sans-serif;
    font-weight: 700;
    text-transform: uppercase;
    line-height: 1;
    white-space: nowrap;
  }
  .tagline {
    position: absolute;
    left: 0; right: 0;
    text-align: center;
    font-family: "Josefin Sans", sans-serif;
    font-weight: 300;
    text-transform: uppercase;
    color: var(--ink-light);
    line-height: 1;
    white-space: nowrap;
  }
  .web {
    position: absolute;
    left: 0; right: 0;
    text-align: center;
    font-family: "Josefin Sans", sans-serif;
    font-size: 17px;
    letter-spacing: 2.5px;
    color: var(--ink-light);
  }

  /* Front */
  .card--front .brand-name {
    top: 134px;
    font-size: 35px;
    color: var(--brand-yellow);
    letter-spacing: 1px;
  }

  /* Contact side */
  .band {
    position: absolute;
    left: 0; right: 0;
    background: var(--paper);
    color: var(--ink-mid);
    display: flex;
    align-items: center;
    justify-content: center;
  }
  .band--top { top: 0; border-bottom: 5px solid var(--rule); height: 40px; }
  .band--bottom { bottom: 0; border-top: 5px solid var(--rule); height: 40px; font-size: 12.5px; letter-spacing: 1px; color: #333; }
  .holder-name { font-weight: 700; font-size: 17px; }
  .holder-title { font-size: 13px; margin-left: 4px; }
  .card--contact .brand-name {
    top: 106px;
    font-size: 38px;
    color: var(--brand-grey);
  }
  .card--contact .tagline { top: 150px; font-size: 20px; letter-spacing: 8px; }
  .contact-line {
    position: absolute;
    left: 0; right: 0;
    display: flex;
    justify-content: center;
    align-items: center;
    gap: 12px;
    font-size: 13px;
    color: var(--ink-light);
  }
  .contact-line--main { top: 205px; }
  .contact-line--web { top: 228px; letter-spacing: 1px; }
  .contact-item { display: inline-flex; align-items: center; gap: 5px; }
  .contact-item svg { width: 11px; height: 11px; fill: var(--ink-light); }

  /* Lockup back */
  .card--lockup .lockup {
    position: absolute;
    top: 114px; left: 0; right: 0;
    display: flex; justify-content: center; align-items: center; gap: 16px;
  }
  .lockup-dot { width: 40px; height: 40px; border-radius: 50%; background: var(--brand-yellow); }
  .card--lockup .brand-name { position: static; font-size: 32px; color: var(--ink-light); }
  .card--lockup .tagline { top: 162px; font-size: 15px; letter-spacing: 6px; padding-left: 56px; }
  .card--lockup .web { top: 258px; }

  /* Wordmark back */
  .card--wordmark .brand-name { top: 118px; font-size: 38px; color: var(--brand-grey); }
  .card--wordmark .tagline { top: 166px; font-size: 21px; letter-spacing: 8px; }
  .card--wordmark .web { top: 258px; }
</style>
</head>
<body>

  <section class="card card--front" aria-label="Card front">
    <div class="brand-name">The Kestrel Works</div>
  </section>

  <section class="card card--contact" aria-label="Card back with contact details">
    <div class="band band--top">
      <span class="holder-name">Your Name,</span><span class="holder-title">Title</span>
    </div>
    <div class="brand-name">The Kestrel Works</div>
    <div class="tagline">Virtual Studio</div>
    <div class="contact-line contact-line--main">
      <span class="contact-item">
        <svg viewBox="0 0 24 24" aria-hidden="true"><path d="M6.6 10.8a15 15 0 0 0 6.6 6.6l2.2-2.2a1 1 0 0 1 1-.25 11.4 11.4 0 0 0 3.6.57 1 1 0 0 1 1 1V20a1 1 0 0 1-1 1A17 17 0 0 1 3 4a1 1 0 0 1 1-1h3.5a1 1 0 0 1 1 1c0 1.25.2 2.45.57 3.57a1 1 0 0 1-.25 1z"/></svg>
        0123 480576
      </span>
      <span class="contact-item">
        <svg viewBox="0 0 24 24" aria-hidden="true"><path d="M5 11l1.5-4.5A2 2 0 0 1 8.4 5h7.2a2 2 0 0 1 1.9 1.5L19 11a2 2 0 0 1 1 1.7V18h-2v2h-2v-2H8v2H6v-2H4v-5.3A2 2 0 0 1 5 11zm2.1 0h9.8l-1-3.2a1 1 0 0 0-1-.8H9.1a1 1 0 0 0-1 .8zM7 15.5a1.3 1.3 0 1 0 0-2.6 1.3 1.3 0 0 0 0 2.6zm10 0a1.3 1.3 0 1 0 0-2.6 1.3 1.3 0 0 0 0 2.6z"/></svg>
        0123 480576
      </span>
      <span class="contact-item">
        <svg viewBox="0 0 24 24" aria-hidden="true"><path d="M3 6h18v12H3zm2 2v.4l7 4.6 7-4.6V8zm0 2.8V16h14v-5.2l-7 4.6z"/></svg>
        info@kestrelworks.com
      </span>
    </div>
    <div class="contact-line contact-line--web">
      <span class="contact-item">
        <svg viewBox="0 0 24 24" aria-hidden="true"><path d="M12 2a10 10 0 1 0 0 20 10 10 0 0 0 0-20zm6.9 9h-3a15 15 0 0 0-1.3-5.6A8 8 0 0 1 18.9 11zM12 4.1c.9 1.2 1.8 3.6 1.9 6.9h-3.8C10.2 7.7 11.1 5.3 12 4.1zM9.4 5.4A15 15 0 0 0 8.1 11h-3a8 8 0 0 1 4.3-5.6zM5.1 13h3a15 15 0 0 0 1.3 5.6A8 8 0 0 1 5.1 13zm6.9 6.9c-.9-1.2-1.8-3.6-1.9-6.9h3.8c-.1 3.3-1 5.7-1.9 6.9zm2.6-1.3a15 15 0 0 0 1.3-5.6h3a8 8 0 0 1-4.3 5.6z"/></svg>
        www.kestrelworks.com
      </span>
    </div>
    <div class="band band--bottom">00, Complex name, City, State 0042</div>
  </section>

  <section class="card card--lockup" aria-label="Card back with full lockup">
    <div class="lockup">
      <span class="lockup-dot" aria-hidden="true"></span>
      <span class="brand-name">The Kestrel Works</span>
    </div>
    <div class="tagline">Virtual Studio</div>
    <div class="web">www.kestrelworks.com</div>
  </section>

  <section class="card card--wordmark" aria-label="Card back with wordmark">
    <div class="brand-name">The Kestrel Works</div>
    <div class="tagline">Virtual Studio</div>
    <div class="web">www.kestrelworks.com</div>
  </section>

</body>
</html>
```